Envelope Design - Winner can do follow-up business

- Varnoko.com is a Swiss-based online store selling business shirts and accessories for business men
- Please visit the webpage to make yourself familiar with the company. Although the text is in German, with Plimbo translator you should be able to understand the main content.
- Our clients are mainly business men between 30 and 60 years old. Mostly with a high income working in the service industry (banking, insurance, lawyers, etc.). Sometimes there wives purchase the shirts for them ;-)
- The colors and the logo are given, as they are also used for the print materials (please see files in attachment)
- I am running several businesses and often need a talented web designer --> the winner gets substantial follow-up business
your task:
-for our company we need a new envelope design
-It should be simple and modern
-please use one of the logos in the followings.
-suprise me :)

```html
<!DOCTYPE html>
<html lang="en">
<head>
<meta charset="utf-8">
<title>Varnoko Envelope Set</title>
<link rel="stylesheet" href="https://fonts.googleapis.com/css2?family=Montserrat:wght@600&family=Open+Sans:wght@400&display=swap">
<style>
  :root {
    --backdrop: #4b2c1b;
    --paper: #ffffff;
    --edge: #9a9a9a;
    --brand-yellow: #e8d86a;
    --brand-red: #ee2e24;
    --ink: #1c1c1c;
  }
  html, body {
    margin: 0;
    padding: 0;
    overflow: hidden;
    background: var(--backdrop);
  }
  .stage {
    position: relative;
    width: 1200px;
    height: 935px;
    overflow: hidden;
    background: var(--backdrop);
  }
  .envelope-art {
    position: absolute;
    inset: 0;
  }
  .brand-name {
    position: absolute;
    margin: 0;
    font-family: "Montserrat", sans-serif;
    font-weight: 600;
    letter-spacing: 2px;
    line-height: 1;
  }
  .brand-name--flap {
    left: 0;
    width: 1308px;
    top: 86px;
    text-align: center;
    font-size: 48px;
    color: var(--brand-red);
  }
  .brand-name--front {
    left: 160px;
    top: 511px;
    font-size: 46px;
    color: var(--brand-yellow);
  }
  .contact-line {
    position: absolute;
    left: 196px;
    margin: 0;
    font-family: "Open Sans", sans-serif;
    font-size: 20px;
    color: var(--ink);
    line-height: 1;
  }
  .contact-line--web { top: 573px; }
  .contact-line--address { top: 830px; }
</style>
</head>
<body>
<main class="stage">
  <svg class="envelope-art" width="1200" height="935" viewBox="0 0 1200 935" aria-hidden="true">
    <!-- back envelope -->
    <rect class="envelope-back" x="140" y="36" width="1028" height="483" fill="var(--paper)"/>
    <path class="flap-yellow" fill="var(--brand-yellow)"
      d="M140 36 H1168 C1158 80 1150 112 1100 125 L680 194 Q654 199 628 194 L215 125 C165 112 158 80 140 36 Z"/>

    <!-- middle envelope -->
    <rect class="envelope-middle" x="43.5" y="216.5" width="1028" height="483" fill="var(--paper)" stroke="var(--edge)" stroke-width="1"/>
    <path class="flap-red" fill="var(--brand-red)"
      d="M43 216 H1072 C1062 260 1055 292 1005 305 L585 373 Q557 378 529 373 L115 305 C68 292 60 260 43 216 Z"/>

    <!-- front envelope -->
    <rect class="envelope-front" x="132.5" y="399.5" width="1027" height="483" fill="var(--paper)" stroke="var(--edge)" stroke-width="1"/>
    <polygon class="corner-accent" fill="var(--brand-yellow)"
      points="778,845 1121,845 1121,688 1160,688 1160,883 749,883"/>

    <!-- globe icon -->
    <g class="icon-globe" fill="none" stroke="var(--brand-red)" stroke-width="1.6">
      <circle cx="172" cy="584" r="10"/>
      <ellipse cx="172" cy="584" rx="4.5" ry="10"/>
      <line x1="162" y1="584" x2="182" y2="584"/>
      <path d="M164 578 H180 M164 590 H180"/>
    </g>

    <!-- pin icon -->
    <g class="icon-pin">
      <path fill="var(--brand-red)" d="M169 830 C162.5 830 158 834.5 158 840.5 C158 848 169 858 169 858 C169 858 180 848 180 840.5 C180 834.5 175.5 830 169 830 Z"/>
      <circle cx="169" cy="840.5" r="4" fill="var(--paper)"/>
    </g>
  </svg>

  <p class="brand-name brand-name--flap">VARNOKO</p>
  <p class="brand-name brand-name--front">VARNOKO</p>
  <p class="contact-line contact-line--web">www.varnoko.com</p>
  <p class="contact-line contact-line--address">Street Name, City Name, State Zipcode</p>
</main>
</body>
</html>
```